Modern Medical Optometry Website

We need mordern, Patient friendly website. Easy to navigate and enhance our advance medical technology and excellent patient care.
1. HOME PAGE
2. OUR TEAM PAGE
3. EYECARE PAGE - VISION SERVICES, EYE EXAMS, KERATOCONUS CENTER, GLAUCOMA , DIABITES, MELORIDEX EXAM, DIGITAL RETINAL, OCT.
4. MYOPIA CONTROL CLINIC
5. DRY EYE CLINIC
6. EYEWEAR
7. PATIENT CENTER - BLOG
7. CONTACT US
This is our current website www.brivaloka.com
and We want to add more content and a cleaner design like these website
http://tarnwickfolvendale.com/
https://www.qmvorlu.com/

```html
<!DOCTYPE html>
<html lang="en">
<head>
<meta charset="utf-8">
<title>Lumivue Optometry</title>
<link rel="stylesheet" href="https://fonts.googleapis.com/css2?family=Raleway:wght@400;500;600;700&family=Open+Sans:wght@400;600&display=swap">
<style>
:root{
  --teal:#2b9db9;
  --teal-dark:#1f87a1;
  --teal-soft:#7cc4d6;
  --yellow:#f6d935;
  --ink:#2f3a40;
  --muted:#7b868c;
  --light:#f4f6f7;
  --dark:#141617;
  --white:#ffffff;
}
*{box-sizing:border-box;margin:0;padding:0}
html,body{width:1200px;height:4358px;overflow:hidden}
body{font-family:"Open Sans",Arial,sans-serif;color:var(--ink);background:var(--white);position:relative}
h1,h2,h3,.raleway{font-family:"Raleway",Arial,sans-serif}
.abs{position:absolute}

/* header */
.topbar{left:0;top:0;width:1200px;height:52px}
.topbar-strip{position:absolute;left:470px;top:0;width:730px;height:40px;background:var(--teal);display:flex;align-items:center;gap:34px;padding-left:40px;color:#fff;font-size:15px}
.topbar-strip span{display:flex;align-items:center;gap:10px}
.social-row{display:flex;gap:14px;margin-left:20px}
.social-dot{width:20px;height:20px;border-radius:50%;border:1.5px solid rgba(255,255,255,.8)}
.brand{left:73px;top:14px;width:114px;height:160px;background:#fff;box-shadow:0 2px 10px rgba(0,0,0,.12);display:flex;flex-direction:column;align-items:center;justify-content:center;gap:10px}
.brand-square{width:52px;height:52px;background:var(--yellow)}
.brand-name{font-family:"Raleway",sans-serif;font-weight:600;font-size:15px;color:var(--ink);text-align:center;line-height:1.2}
.nav{left:218px;top:104px;display:flex;gap:42px;font-family:"Raleway",sans-serif;font-size:16px;font-weight:500;color:#6c777d}
.nav .active{color:var(--teal);font-weight:700}
.search-icon{left:1096px;top:104px}

/* hero */
.hero{left:0;top:189px;width:1200px;height:572px;background:linear-gradient(90deg,#2a95b1,#43aac2)}
.hero h1{position:absolute;left:80px;top:125px;color:#fff;font-size:66px;font-weight:600;line-height:1.12;letter-spacing:2px}
.hero p{position:absolute;left:80px;top:280px;width:470px;color:#fff;font-size:15px;line-height:1.7}
.btn-yellow{background:var(--yellow);color:var(--ink);font-family:"Raleway",sans-serif;font-weight:600;font-size:15px;display:flex;align-items:center;justify-content:center}
.hero .btn-yellow{position:absolute;left:80px;top:380px;width:236px;height:54px}
.hero-ring{position:absolute;left:562px;top:17px;width:544px;height:544px;border-radius:50%;border:24px solid var(--yellow);background:#fff;padding:14px}
.hero-photo{width:100%;height:100%;border-radius:50%;background:radial-gradient(circle at 45% 40%,#f1d4bf,#c9a07a 55%,#7c8f9a)}
.dots{position:absolute;left:560px;top:495px;display:flex;gap:14px}
.dots i{width:16px;height:16px;border-radius:50%;border:2px solid #fff;display:block}
.dots i.on{background:#fff}

/* promise */
.promise-kicker{left:80px;top:820px;font-family:"Raleway",sans-serif;font-size:16px;color:var(--muted);letter-spacing:1px}
.promise-title{left:80px;top:862px;font-size:40px;line-height:1.2;font-weight:400;color:var(--ink)}
.promise-title b{color:var(--teal);font-weight:700;display:block}
.promise-copy{left:560px;top:822px;width:560px;font-size:14.5px;line-height:1.75;color:var(--muted)}
.promise-copy p+p{margin-top:18px}

/* info cards */
.info-band{left:78px;top:1148px;width:1041px;height:340px;background:var(--teal)}
.info-card{position:absolute;top:0;width:346px;height:340px;padding:40px 34px;color:#fff}
.info-card h3{font-size:26px;font-weight:500;margin:26px 0 14px}
.info-card p{font-size:13.5px;line-height:1.65}
.info-card .phone{font-family:"Raleway",sans-serif;font-size:28px;font-weight:700;margin-top:26px}
.info-card.feature{top:-35px;height:410px;background:var(--yellow);color:var(--ink);box-shadow:0 8px 22px rgba(0,0,0,.15);padding-top:70px}
.info-card.feature p{color:#4c5256}

/* about */
.about-photo{left:78px;top:1592px;width:524px;height:471px;border-radius:14px;background:linear-gradient(90deg,#f2f5f7 0%,#e8eef2 45%,#9fb3c2 70%,#3b5b78 100%);box-shadow:0 6px 20px rgba(0,0,0,.15)}
.about-kicker{left:660px;top:1726px;font-family:"Raleway",sans-serif;color:var(--muted);font-size:16px;letter-spacing:1px}
.about-title{left:660px;top:1756px;font-size:38px;font-weight:700;color:var(--teal)}
.about-copy{left:660px;top:1822px;width:460px;font-size:14.5px;line-height:1.75;color:var(--teal-soft)}
.about .btn-yellow{position:absolute;left:660px;top:2010px;width:120px;height:52px}

/* services */
.services{left:0;top:2127px;width:1200px;height:939px;background:linear-gradient(180deg,#2a94ae,#3ea7c0)}
.services-kicker{position:absolute;left:0;width:1200px;top:64px;text-align:center;color:#d9f0f5;font-family:"Raleway",sans-serif;font-size:16px;letter-spacing:1px}
.services-title{position:absolute;left:0;width:1200px;top:90px;text-align:center;color:#fff;font-size:38px;font-weight:700}
.tile{position:absolute;width:326px;height:326px;border-radius:6px;box-shadow:0 6px 16px rgba(0,0,0,.2)}
.tile.highlight{border:8px solid #5bbdd3;background:var(--yellow);display:flex;align-items:center;justify-content:center;font-family:"Raleway",sans-serif;font-size:28px;font-weight:500;color:var(--ink)}

/* testimonials */
.testi{left:0;top:3066px;width:1200px;height:514px;background:var(--light)}
.testi-kicker{position:absolute;left:0;width:1200px;top:68px;text-align:center;font-family:"Raleway",sans-serif;color:var(--muted);font-size:16px;letter-spacing:1px}
.testi-title{position:absolute;left:0;width:1200px;top:94px;text-align:center;font-size:38px;font-weight:700;color:var(--teal)}
.quote-card{position:absolute;top:183px;width:340px;height:186px;background:#fff;box-shadow:0 4px 14px rgba(0,0,0,.1);padding:26px 28px 0 80px;font-size:13.5px;line-height:1.65;color:var(--muted)}
.quote-mark{position:absolute;left:0;top:44px;width:48px;height:58px;background:var(--yellow);display:flex;align-items:center;justify-content:center;font-family:"Raleway",sans-serif;font-weight:700;font-size:34px;color:var(--ink)}
.quote-ghost{position:absolute;right:22px;bottom:2px;font-family:"Raleway",sans-serif;font-size:110px;line-height:1;color:#cfe7ee}
.author{position:absolute;top:386px;display:flex;align-items:center;gap:22px}
.author-photo{width:62px;height:62px;border:3px solid #fff;box-shadow:0 2px 6px rgba(0,0,0,.2);background:linear-gradient(135deg,#d9e6ee,#8fb2c6)}
.author b{display:block;font-family:"Raleway",sans-serif;color:var(--teal);font-size:18px;font-weight:600}
.stars{color:var(--yellow);font-size:15px;letter-spacing:1px}
.stars .off{color:#c9cfd2}

/* brands */
.brand-names{left:60px;top:3652px;width:1080px;display:flex;justify-content:space-between;font-family:"Raleway",sans-serif;font-weight:700;font-size:22px;color:#1c1c1c;letter-spacing:1px}
.frames{left:78px;top:3745px;width:1050px;display:flex;justify-content:space-between}
.frame{width:108px;height:48px;border-radius:24px;background:linear-gradient(90deg,#3a3f44,#7d858b)}

/* footer */
.footer{left:0;top:3880px;width:1200px;height:415px;background:var(--dark);color:#cfd4d6}
.fcol{position:absolute;top:62px;width:320px}
.fcol h3{font-size:19px;color:var(--teal);font-weight:600;margin-bottom:28px}
.fline{display:flex;gap:18px;font-size:14px;margin-bottom:20px;align-items:flex-start;line-height:1.5}
.fline svg{flex:none;margin-top:2px}
.dir-btn{margin-top:16px;width:280px;height:42px;border-radius:21px;background:#2c3134;display:flex;align-items:center;justify-content:space-between;padding:0 22px;font-size:13.5px}
.hours p{font-size:14px;margin-bottom:12px}
.hours b{color:var(--yellow);font-weight:600}
.fsocial{display:flex;gap:14px;margin-top:22px}
.fsocial i{width:38px;height:38px;border-radius:50%;background:var(--teal);display:block}
.copyright{left:0;top:4295px;width:1200px;height:63px;background:#0c0d0e;color:#8a9195;font-size:13.5px;display:flex;align-items:center;justify-content:center}
.copyright b{color:var(--yellow);font-weight:600;margin:0 5px}
</style>
</head>
<body>

<header>
  <div class="abs topbar">
    <div class="topbar-strip">
      <span><svg width="16" height="16" viewBox="0 0 24 24" fill="#fff"><path d="M6.6 10.8a15 15 0 006.6 6.6l2.2-2.2c.3-.3.7-.4 1-.2 1.1.4 2.3.6 3.6.6.6 0 1 .4 1 1V20c0 .6-.4 1-1 1A17 17 0 013 4c0-.6.4-1 1-1h3.5c.6 0 1 .4 1 1 0 1.3.2 2.5.6 3.6.1.3 0 .7-.2 1z"/></svg>555-210-4830</span>
      <span><svg width="18" height="14" viewBox="0 0 24 18" fill="none" stroke="#fff" stroke-width="2"><rect x="1" y="1" width="22" height="16"/><path d="M1 1l11 9 11-9"/></svg>info@lumivueoptometry.com</span>
      <div class="social-row"><i class="social-dot"></i><i class="social-dot"></i><i class="social-dot"></i><i class="social-dot"></i></div>
    </div>
  </div>
  <div class="abs brand">
    <div class="brand-square"></div>
    <div class="brand-name">LUMIVUE<br>OPTOMETRY</div>
  </div>
  <nav class="abs nav">
    <span class="active">HOME</span><span>OUR TEAM</span><span>EYE CARE</span><span>MYOPIA CONTROL CLINIC</span><span>EYEWEAR</span><span>BLOG</span><span>CONTACT US</span>
  </nav>
  <svg class="abs search-icon" width="20" height="20" viewBox="0 0 24 24" fill="none" stroke="#2b9db9" stroke-width="2.5"><circle cx="10" cy="10" r="7"/><path d="M15 15l7 7"/></svg>
</header>

<section class="abs hero">
  <h1>LUMIVUE<br>OPTOMETRY</h1>
  <p>Lorem ipsum dolor sit amet, consectetur adipiscing elit, sed aliqua. Ut enim ad minim veniam, quis nostrud exercitation ullamco laboris nisi ut aliquip ex ea commodo consequat.</p>
  <div class="btn-yellow">MAKE AN APPOINTMENT</div>
  <div class="hero-ring"><div class="hero-photo" role="img" aria-label="Photo of a mother and daughter smiling during an eye check"></div></div>
  <div class="dots"><i></i><i class="on"></i><i></i></div>
</section>

<section class="promise">
  <div class="abs promise-kicker">THE LUMIVUE PROMISE</div>
  <h2 class="abs promise-title">NOT JUST BETTER CARE,<b>BUT A BETTER CARE<br>EXPERIENCE</b></h2>
  <div class="abs promise-copy">
    <p>Welcome to Lumivue Optometry, where your vision and eye health are our sole priority. We take great pride in providing you with state-of-the-art eyecare matched with personal attention from our staff and doctors. Your quality of life is our goal and we believe that healthy eyesight is vital to achieving it.</p>
    <p>Our professional and personable staff is highly trained in helping you achieve and maintain healthy eyesight. Our optometrists have combined experiences and specialize in Orthokeratology (OrthoK), Ocular disease, Glaucoma diagnosis &amp; management.</p>
  </div>
</section>

<section class="abs info-band">
  <div class="info-card" style="left:0">
    <svg width="72" height="46" viewBox="0 0 72 46" fill="none" stroke="#fff" stroke-width="3"><path d="M3 23C14 7 58 7 69 23C58 39 14 39 3 23z"/><circle cx="36" cy="23" r="10"/></svg>
    <h3>Emergency Cases</h3>
    <p>Caring Your Eyes is Important consectetur adipiscing Keep calm and Care your Eyes</p>
    <div class="phone">555-210-4830</div>
  </div>
  <div class="info-card feature" style="left:343px">
    <svg width="64" height="56" viewBox="0 0 64 56" fill="none" stroke="#2f3a40" stroke-width="3"><circle cx="32" cy="28" r="22"/><circle cx="32" cy="28" r="9"/><path d="M2 28h8M54 28h8"/></svg>
    <h3>Doctor Timetable</h3>
    <p>Professional and Certificated Doctor consectetur adipiscing elit, sed do eiusmod tempor incididunt ut labore et dolore magna aliqua.</p>
  </div>
  <div class="info-card" style="left:695px">
    <svg width="80" height="40" viewBox="0 0 80 40" fill="none" stroke="#fff" stroke-width="3"><circle cx="20" cy="22" r="14"/><circle cx="60" cy="22" r="14"/><path d="M34 20q6-6 12 0M6 16L2 6M74 16l4-10"/></svg>
    <h3>Opening Hours</h3>
    <p>Monday - Thursday : 9 am - 6 pm</p>
    <p style="margin-top:8px">Friday : 8.30 am - 5 pm</p>
    <p style="margin-top:8px">Closed on Sundays</p>
    <p style="margin-top:8px">Please keep in mind we are closed for lunch 1-2 pm</p>
  </div>
</section>

<section class="about">
  <div class="abs about-photo" role="img" aria-label="Photo of a child covering one eye in front of an eye chart"></div>
  <div class="abs about-kicker">ABOUT</div>
  <h2 class="abs about-title">LUMIVUE OPTOMETRY</h2>
  <p class="abs about-copy">Lorem ipsum dolor sit amet, consectetur adipiscing elit, sed do eiusmod tempor incididunt ut labore et dolore magna aliqua. Ut enim ad minim veniam, quis nostrud exercitation ullamco laboris nisi ut aliquip ex ea commodo consequat. Duis aute irure dolor in reprehenderit in voluptate velit esse cillum dolore eu fugiat nulla pariatur. Excepteur sint occaecat cupidatat non proident.</p>
  <div class="btn-yellow">VISITBOOK</div>
</section>

<section class="abs services">
  <div class="services-kicker">WHAT WE OFFER</div>
  <h2 class="services-title">LUMIVUE SERVICES</h2>
  <div class="tile" style="left:78px;top:177px;background:linear-gradient(160deg,#dfe8ec,#5a8fb0 60%,#2d6d93)" role="img" aria-label="Photo of the clinic team in medical scrubs"></div>
  <div class="tile highlight" style="left:439px;top:177px">DRY EYES</div>
  <div class="tile" style="left:799px;top:177px;background:linear-gradient(135deg,#f5f5f5,#c8ccce 60%,#6f7478)" role="img" aria-label="Photo of eyeglasses resting on an eye chart"></div>
  <div class="tile" style="left:78px;top:538px;background:linear-gradient(135deg,#d9dfe3,#9aa7b0 50%,#e8cdb6)" role="img" aria-label="Photo of a patient at a slit lamp examination"></div>
  <div class="tile" style="left:439px;top:538px;background:linear-gradient(135deg,#e6d9d2,#d2b3a3 55%,#a9c6d4)" role="img" aria-label="Photo of a contact lens on a fingertip"></div>
  <div class="tile" style="left:799px;top:538px;background:linear-gradient(135deg,#f1ece6,#c3b2a3 50%,#3e6d8f)" role="img" aria-label="Photo of a doctor examining a young patient"></div>
</section>

<section class="abs testi">
  <div class="testi-kicker">TESTIMONIAL</div>
  <h2 class="testi-title">CLIENTS FEEDBACK</h2>

  <div class="quote-card" style="left:78px"><div class="quote-mark">“</div>Lorem ipsum dolor sit amet, type to consectetur adipiscing elit, sed do eiusmod tempor incididunt ut labore et dolore magna aliqua. Ut enim ad minim veniam, quis nostrud.<div class="quote-ghost">”</div></div>
  <div class="quote-card" style="left:430px"><div class="quote-mark">“</div>Lorem ipsum dolor sit amet, type to consectetur adipiscing elit, sed do eiusmod tempor incididunt ut labore et dolore magna aliqua. Ut enim ad minim veniam, quis nostrud.<div class="quote-ghost">”</div></div>
  <div class="quote-card" style="left:786px"><div class="quote-mark">“</div>Lorem ipsum dolor sit amet, type to consectetur adipiscing elit, sed do eiusmod tempor incididunt ut labore et dolore magna aliqua. Ut enim ad minim veniam, quis nostrud.<div class="quote-ghost">”</div></div>

  <div class="author" style="left:118px"><div class="author-photo" role="img" aria-label="Client portrait"></div><div><b>Tarek Winslow</b><span class="stars">★★★★<span class="off">★</span></span></div></div>
  <div class="author" style="left:470px"><div class="author-photo" role="img" aria-label="Client portrait"></div><div><b>Tarek Winslow</b><span class="stars">★★★★<span class="off">★</span></span></div></div>
  <div class="author" style="left:826px"><div class="author-photo" role="img" aria-label="Client portrait"></div><div><b>Tarek Winslow</b><span class="stars">★★★★<span class="off">★</span></span></div></div>
</section>

<section class="eyewear-brands">
  <div class="abs brand-names"><span>MARLOW</span><span>KESTRA</span><span>ORVEN &amp; CO.</span><span>VELOTTI</span><span>SOLEINE</span><span>BRISKWAY</span></div>
  <div class="abs frames">
    <div class="frame" role="img" aria-label="Product photo of sunglasses"></div>
    <div class="frame" role="img" aria-label="Product photo of eyeglass frames" style="background:linear-gradient(90deg,#5a3a2a,#a07050)"></div>
    <div class="frame" role="img" aria-label="Product photo of sunglasses" style="background:linear-gradient(90deg,#6b4a36,#b08a6a)"></div>
    <div class="frame" role="img" aria-label="Product photo of light eyeglass frames" style="background:linear-gradient(90deg,#d8d2c8,#efe9df)"></div>
    <div class="frame" role="img" aria-label="Product photo of black eyeglass frames" style="background:linear-gradient(90deg,#1e1e1e,#5a5a5a)"></div>
    <div class="frame" role="img" aria-label="Product photo of tinted sunglasses" style="background:linear-gradient(90deg,#b9a48c,#e2d3bf)"></div>
  </div>
</section>

<footer class="abs footer">
  <div class="fcol" style="left:80px">
    <h3>Lumivue Optometry</h3>
    <div class="fline"><svg width="18" height="18" viewBox="0 0 24 24" fill="#f6d935"><path d="M6.6 10.8a15 15 0 006.6 6.6l2.2-2.2c.3-.3.7-.4 1-.2 1.1.4 2.3.6 3.6.6.6 0 1 .4 1 1V20c0 .6-.4 1-1 1A17 17 0 013 4c0-.6.4-1 1-1h3.5c.6 0 1 .4 1 1 0 1.3.2 2.5.6 3.6.1.3 0 .7-.2 1z"/></svg>555-210-4830</div>
    <div class="fline"><svg width="18" height="18" viewBox="0 0 24 24" fill="#f6d935"><path d="M6.6 10.8a15 15 0 006.6 6.6l2.2-2.2c.3-.3.7-.4 1-.2 1.1.4 2.3.6 3.6.6.6 0 1 .4 1 1V20c0 .6-.4 1-1 1A17 17 0 013 4c0-.6.4-1 1-1h3.5c.6 0 1 .4 1 1 0 1.3.2 2.5.6 3.6.1.3 0 .7-.2 1z"/></svg>555-210-4830</div>
    <div class="fline"><svg width="18" height="14" viewBox="0 0 24 18" fill="#f6d935"><rect width="24" height="18"/></svg>info@brivaloka.com</div>
    <div class="fline"><svg width="16" height="20" viewBox="0 0 16 22" fill="#f6d935"><path d="M8 0a8 8 0 00-8 8c0 6 8 14 8 14s8-8 8-14a8 8 0 00-8-8zm0 11a3 3 0 110-6 3 3 0 010 6z"/></svg>4820 Alder Crest Ave., Fernvale,<br>CA 90000</div>
    <div class="dir-btn">Get directions on the map <svg width="40" height="10" viewBox="0 0 40 10" fill="none" stroke="#2b9db9" stroke-width="2"><path d="M0 5h38M33 1l5 4-5 4"/></svg></div>
  </div>
  <div class="fcol" style="left:436px">
    <h3>Northgate</h3>
    <div class="fline"><svg width="18" height="18" viewBox="0 0 24 24" fill="#f6d935"><path d="M6.6 10.8a15 15 0 006.6 6.6l2.2-2.2c.3-.3.7-.4 1-.2 1.1.4 2.3.6 3.6.6.6 0 1 .4 1 1V20c0 .6-.4 1-1 1A17 17 0 013 4c0-.6.4-1 1-1h3.5c.6 0 1 .4 1 1 0 1.3.2 2.5.6 3.6.1.3 0 .7-.2 1z"/></svg>555-274-9160</div>
    <div class="fline"><svg width="18" height="14" viewBox="0 0 24 18" fill="#f6d935"><rect width="24" height="18"/></svg>northgate@brivaloka.com</div>
    <div class="fline"><svg width="16" height="20" viewBox="0 0 16 22" fill="#f6d935"><path d="M8 0a8 8 0 00-8 8c0 6 8 14 8 14s8-8 8-14a8 8 0 00-8-8zm0 11a3 3 0 110-6 3 3 0 010 6z"/></svg>2291 Quillon St., Suite 4,<br>Northgate, CA 90001</div>
    <div class="dir-btn" style="margin-top:56px">Get directions on the map <svg width="40" height="10" viewBox="0 0 40 10" fill="none" stroke="#2b9db9" stroke-width="2"><path d="M0 5h38M33 1l5 4-5 4"/></svg></div>
  </div>
  <div class="fcol hours" style="left:790px">
    <h3>Opening Hours</h3>
    <p>Monday - Thursday : <b>9 am - 6 pm</b></p>
    <p>Friday : <b>8.30 am - 5 pm</b></p>
    <p>Saturday : <b>8.30 am - 5 pm</b></p>
    <p>Closed on <b>Sundays</b></p>
    <p>Please keep in mind we are<br>closed for <b>lunch 1-2 pm</b></p>
    <div class="fsocial"><i></i><i></i><i></i><i></i></div>
  </div>
</footer>
<div class="abs copyright">Copyright © <b>LUMIVUE OPTOMETRY</b> - 2019 . All Right Reserved</div>

</body>
</html>
```